Fun Employee News and Engagement Portal - Tidy Hearth Company

We are looking for a clean, but fun WordPress template for an internal employee engagement website. The site will be a place we share news, fun stories and pictures. We'll provide space for our employees to post comments, etc.
We are a deep dish pizza restaurant with a rich history. I'd love to see your take on a look and feel for us! The site will be called Bim-Zee. I've posted some images and colors along with this brief description.
Focus on making the template whimsical and fun! (Extra point for focusing on the "Lettering in lights" ).
I will continue to post additional pieces of art and content examples.
Reason: Our team is continuing to review designs. We've decided to extend the timing a few more days. Good luck! Make it playful!
Reason: We need more time with our team to review these designs. We are going to extend one more time!
Reason: Still trying to get enough time to review with the Bim-Zee team!
Reason: We are continuing to evaluate designs. Thank you!
Industry/Entity Type
American Restaurant
Number of Pages Required
1 page
Look and feel
Each slider illustrates characteristics of the customer's brand and the style your logo design should communicate.

```html
<!DOCTYPE html>
<html lang="en">
<head>
<meta charset="utf-8">
<title>Bim-Zee — Employee Portal</title>
<link href="https://fonts.googleapis.com/css2?family=Roboto:wght@400;500;700;900&display=swap" rel="stylesheet">
<style>
:root{
  --red:#d8232a;
  --red-dark:#b81b21;
  --ink:#2b2b2b;
  --muted:#8a8a8a;
  --line:#e6e6e6;
  --page:#efefef;
  --card:#ffffff;
  --star:#f5a623;
  --wood-dark:#2e1b10;
  --wood:#6a4429;
}
*{box-sizing:border-box;margin:0;padding:0}
html,body{width:1200px;height:2460px;overflow:hidden}
body{font-family:'Roboto',Arial,sans-serif;color:var(--ink);background:var(--page);font-size:12px}
.wrap{width:1020px;margin:0 auto;position:relative}

/* header */
.site-header{height:88px;background:var(--card);box-shadow:0 1px 4px rgba(0,0,0,.12);position:relative;z-index:2}
.site-header .wrap{display:flex;align-items:center;height:88px}
.brand{width:270px;display:flex;align-items:center;gap:10px;font-size:24px;font-weight:500;color:var(--ink);white-space:nowrap}
.brand-mark{width:14px;height:14px;background:var(--red);flex:none}
.burger{width:26px;display:flex;flex-direction:column;gap:5px;margin-right:56px}
.burger span{height:3px;background:var(--ink);display:block}
.nav-item{font-size:11px;font-weight:500;text-transform:uppercase;color:#555;display:flex;align-items:center;gap:7px;margin-right:56px;white-space:nowrap}
.nav-item svg{width:14px;height:14px}
.search{margin-left:auto;width:150px;height:28px;border:1px solid #ccc;display:flex;align-items:center;justify-content:space-between;padding:0 8px;font-size:11px;color:#999}

/* hero */
.hero{height:460px;position:relative;overflow:hidden}
.hero-photo{position:absolute;inset:0;background:
  radial-gradient(circle at 80% 42%,#c9553a 0,#a8402c 110px,#7a4a2c 200px,transparent 260px),
  linear-gradient(100deg,var(--wood-dark) 0%,#4a2d1a 45%,var(--wood) 100%)}
.hero-copy{position:absolute;left:100px;top:150px;width:420px;color:#fff}
.hero-copy h1{font-size:38px;font-weight:900;letter-spacing:1px;margin-bottom:14px;white-space:nowrap}
.hero-copy p{font-size:13px;line-height:18px;color:#eee;margin-bottom:18px;width:360px}
.btn{display:inline-block;background:var(--red);color:#fff;font-size:10px;font-weight:700;text-transform:uppercase;padding:8px 14px;border-radius:2px}
.dots{display:flex;gap:8px;margin-top:22px}
.dots span{width:11px;height:11px;border-radius:50%;border:2px solid #fff}
.dots span.on{background:#fff}

/* section title */
.section-title{text-align:center;font-size:28px;font-weight:700;letter-spacing:1px;padding:44px 0 24px}

/* proposals */
.proposals{display:flex;gap:20px;height:280px}
.proposal{flex:1;background:var(--card);box-shadow:0 1px 3px rgba(0,0,0,.1)}
.proposal .photo{height:190px}
.proposal .row{display:flex;justify-content:space-between;align-items:center;padding:10px 12px 6px}
.stars{color:var(--star);font-size:12px;letter-spacing:1px}
.stars i{color:#ccc;font-style:normal}
.mini-btn{background:var(--red);color:#fff;font-size:9px;font-weight:700;padding:4px 8px;text-transform:uppercase}
.proposal p{font-size:11px;line-height:15px;color:#777;padding:0 12px}

/* columns */
.columns{display:flex;gap:24px;margin-top:30px}
.col-side{width:240px;display:flex;flex-direction:column;gap:30px}
.col-main{width:480px;display:flex;flex-direction:column;gap:30px}
.box{background:var(--card);box-shadow:0 1px 3px rgba(0,0,0,.1);padding:16px;position:relative}
.box h3{font-size:15px;font-weight:700;text-transform:uppercase;letter-spacing:.5px;padding-bottom:10px;border-bottom:1px solid var(--line);margin-bottom:6px}
.see-all{position:absolute;right:16px;bottom:14px;font-size:11px;font-weight:700;color:var(--red);text-transform:uppercase}
.list-item{display:flex;align-items:center;gap:10px;height:52px;border-bottom:1px solid var(--line)}
.thumb{width:40px;height:40px;border-radius:3px;flex:none}
.list-item .text{flex:1}
.list-item .title{font-size:13px;font-weight:500;margin-bottom:3px}
.arrow{color:#999;font-size:18px}
.story .title{font-size:11px;font-weight:700;text-transform:uppercase}
.story .sub{font-size:10px;color:var(--muted)}
.story .thumb{width:34px;height:34px}
.story svg{width:14px;height:14px;flex:none}

/* posts */
.post{padding:18px 20px}
.author{display:flex;align-items:center;gap:12px;margin-bottom:10px}
.avatar{width:42px;height:42px;border-radius:50%;background:#c7b3a3;flex:none}
.author .name{font-size:13px;font-weight:700;color:var(--ink)}
.author .meta{font-size:10px;color:var(--muted);margin-top:3px}
.post p{font-size:11px;line-height:16px;color:#777}
.post .photo{margin:12px 0;border-radius:2px}
.post h4{font-size:13px;font-weight:700;text-transform:uppercase;margin-bottom:6px}
.actions{display:flex;gap:24px;font-size:10px;font-weight:700;color:#666;text-transform:uppercase;border-top:1px solid var(--line);margin-top:12px;padding-top:10px}
.comment{margin-top:10px;height:30px;border:1px solid var(--line);display:flex;align-items:center;gap:8px;padding:0 6px;font-size:10px;color:#aaa}
.comment .avatar{width:20px;height:20px}
.collage{display:grid;grid-template-columns:1fr 1fr;grid-template-rows:1fr 1fr 1fr;gap:6px;height:330px;margin:12px 0}
.collage .big{grid-row:1/4}

/* footer */
.partners{position:absolute;top:2170px;left:0;width:1200px;height:150px;background:var(--card);display:flex;justify-content:center;align-items:center;gap:60px}
.badge{height:60px;background:#d9d9d9}
.site-footer{position:absolute;top:2320px;left:0;width:1200px;height:140px;background:var(--red);color:#fff;text-align:center}
.links{font-size:12px;padding-top:28px}
.links span{margin:0 10px}
.social{display:flex;justify-content:center;gap:12px;margin:14px 0}
.social span{width:24px;height:24px;border-radius:50%;border:2px solid #fff}
.copy{font-size:11px}
.to-top{position:absolute;right:92px;top:26px;font-size:14px}
</style>
</head>
<body>

<header class="site-header">
  <div class="wrap">
    <div class="brand"><span class="brand-mark"></span>Bim-Zee</div>
    <div class="burger"><span></span><span></span><span></span></div>
    <div class="nav-item">Choose a city ▾</div>
    <div class="nav-item"><svg viewBox="0 0 16 16"><circle cx="8" cy="5" r="3" fill="#666"/><path d="M2 15c0-4 3-6 6-6s6 2 6 6z" fill="#666"/></svg>Become a member</div>
    <div class="nav-item"><svg viewBox="0 0 16 16"><rect x="3" y="7" width="10" height="8" fill="#666"/><path d="M5 7V5a3 3 0 016 0v2" stroke="#666" stroke-width="2" fill="none"/></svg>Login</div>
    <div class="search">Enter Name <svg width="12" height="12" viewBox="0 0 12 12"><circle cx="5" cy="5" r="3.5" stroke="#888" stroke-width="1.5" fill="none"/><path d="M8 8l3 3" stroke="#888" stroke-width="1.5"/></svg></div>
  </div>
</header>

<section class="hero">
  <div class="hero-photo" role="img" aria-label="Deep dish pizza with tomatoes and herbs on a dark wooden table"></div>
  <div class="hero-copy">
    <h1>EXCEPTEUR SINT</h1>
    <p>Duis aute irure dolor in reprehenderit in voluptate velit esse cillum dolore eu fugiat nulla pariatur. Excepteur sint occaecat cupidatat non proident, sunt.</p>
    <span class="btn">Read more ›</span>
    <div class="dots"><span class="on"></span><span></span><span></span><span></span></div>
  </div>
</section>

<main class="wrap">
  <h2 class="section-title">LATEST PROPOSALS</h2>
  <div class="proposals">
    <article class="proposal"><div class="photo" role="img" aria-label="Friends sharing pizza at a table" style="background:linear-gradient(135deg,#b27a52,#6b4330)"></div><div class="row"><span class="stars">★★★<i>★★</i></span><span class="mini-btn">♥ Save</span></div><p>Lorem ipsum dolor sit amet, consectetur adipiscing elit sed do eiusmod.</p></article>
    <article class="proposal"><div class="photo" role="img" aria-label="Group of coworkers laughing over pizza" style="background:linear-gradient(135deg,#c59a6e,#7d5539)"></div><div class="row"><span class="stars">★★★★<i>★</i></span><span class="mini-btn">♥ Save</span></div><p>Lorem ipsum dolor sit amet, consectetur adipiscing elit sed do eiusmod.</p></article>
    <article class="proposal"><div class="photo" role="img" aria-label="Friends eating pizza slices together" style="background:linear-gradient(135deg,#a86b48,#5a3a2a)"></div><div class="row"><span class="stars">★★★<i>★★</i></span><span class="mini-btn">♥ Save</span></div><p>Lorem ipsum dolor sit amet, consectetur adipiscing elit sed do eiusmod.</p></article>
    <article class="proposal"><div class="photo" role="img" aria-label="Pizza slices on a wooden board" style="background:linear-gradient(135deg,#8a6a58,#4a3a32)"></div><div class="row"><span class="stars">★★★★<i>★</i></span><span class="mini-btn">♥ Save</span></div><p>Lorem ipsum dolor sit amet, consectetur adipiscing elit sed do eiusmod.</p></article>
  </div>

  <div class="columns">
    <div class="col-side">
      <section class="box" style="height:450px">
        <h3>Quick searches</h3>
        <div class="list-item"><div class="thumb" role="img" aria-label="Pizza dish" style="background:#b5653f"></div><div class="text"><div class="title">Quis autem vel</div><div class="stars">★★★<i>★★</i></div></div><span class="arrow">›</span></div>
        <div class="list-item"><div class="thumb" role="img" aria-label="Pizza dish" style="background:#a8553a"></div><div class="text"><div class="title">Quis autem vel</div><div class="stars">★★★★<i>★</i></div></div><span class="arrow">›</span></div>
        <div class="list-item"><div class="thumb" role="img" aria-label="Pizza dish" style="background:#c07048"></div><div class="text"><div class="title">Quis autem vel</div><div class="stars">★★★<i>★★</i></div></div><span class="arrow">›</span></div>
        <div class="list-item"><div class="thumb" role="img" aria-label="Pizza dish" style="background:#9c4e34"></div><div class="text"><div class="title">Quis autem vel</div><div class="stars">★★★★<i>★</i></div></div><span class="arrow">›</span></div>
        <div class="list-item"><div class="thumb" role="img" aria-label="Pizza dish" style="background:#b8683f"></div><div class="text"><div class="title">Quis autem vel</div><div class="stars">★★★<i>★★</i></div></div><span class="arrow">›</span></div>
        <div class="list-item"><div class="thumb" role="img" aria-label="Pizza dish" style="background:#a65a3c"></div><div class="text"><div class="title">Quis autem vel</div><div class="stars">★★★★<i>★</i></div></div><span class="arrow">›</span></div>
        <div class="list-item" style="border:0"><div class="thumb" role="img" aria-label="Pizza dish" style="background:#bb6c44"></div><div class="text"><div class="title">Quis autem vel</div><div class="stars">★★★<i>★★</i></div></div><span class="arrow">›</span></div>
        <span class="see-all">See all pics ›</span>
      </section>
      <section class="box" style="height:660px">
        <h3>Recent posts</h3>
        <div class="list-item"><div class="thumb" role="img" aria-label="Post photo" style="background:#b07a58"></div><div class="text"><div class="title">Nemo enim ipsam</div><div class="stars">★★★<i>★★</i></div></div><span class="arrow">›</span></div>
        <div class="list-item"><div class="thumb" role="img" aria-label="Post photo" style="background:#9a6848"></div><div class="text"><div class="title">Nemo enim ipsam</div><div class="stars">★★★★<i>★</i></div></div><span class="arrow">›</span></div>
        <div class="list-item"><div class="thumb" role="img" aria-label="Post photo" style="background:#c08860"></div><div class="text"><div class="title">Nemo enim ipsam</div><div class="stars">★★★<i>★★</i></div></div><span class="arrow">›</span></div>
        <div class="list-item"><div class="thumb" role="img" aria-label="Post photo" style="background:#8e5c40"></div><div class="text"><div class="title">Nemo enim ipsam</div><div class="stars">★★★★<i>★</i></div></div><span class="arrow">›</span></div>
        <div class="list-item"><div class="thumb" role="img" aria-label="Post photo" style="background:#b8704c"></div><div class="text"><div class="title">Nemo enim ipsam</div><div class="stars">★★★<i>★★</i></div></div><span class="arrow">›</span></div>
        <div class="list-item"><div class="thumb" role="img" aria-label="Post photo" style="background:#a4704e"></div><div class="text"><div class="title">Nemo enim ipsam</div><div class="stars">★★★★<i>★</i></div></div><span class="arrow">›</span></div>
        <div class="list-item"><div class="thumb" role="img" aria-label="Post photo" style="background:#b6603e"></div><div class="text"><div class="title">Nemo enim ipsam</div><div class="stars">★★★<i>★★</i></div></div><span class="arrow">›</span></div>
        <div class="list-item"><div class="thumb" role="img" aria-label="Post photo" style="background:#987050"></div><div class="text"><div class="title">Nemo enim ipsam</div><div class="stars">★★★★<i>★</i></div></div><span class="arrow">›</span></div>
        <div class="list-item"><div class="thumb" role="img" aria-label="Post photo" style="background:#c27a52"></div><div class="text"><div class="title">Nemo enim ipsam</div><div class="stars">★★★<i>★★</i></div></div><span class="arrow">›</span></div>
        <div class="list-item" style="border:0"><div class="thumb" role="img" aria-label="Post photo" style="background:#a06040"></div><div class="text"><div class="title">Nemo enim ipsam</div><div class="stars">★★★★<i>★</i></div></div><span class="arrow">›</span></div>
        <span class="see-all">See all posts ›</span>
      </section>
    </div>

    <div class="col-main">
      <article class="box post" style="height:450px">
        <div class="author"><div class="avatar"></div><div><div class="name">Dale Ortiz ▾</div><div class="meta">Shared a photo · 2 hours ago</div></div></div>
        <p>Lorem ipsum dolor sit amet, consectetur adipiscing elit, sed do eiusmod tempor incididunt ut labore et dolore magna aliqua.</p>
        <div class="photo" role="img" aria-label="Two coworkers sharing a pizza slice" style="height:170px;background:linear-gradient(135deg,#c8986e,#7e4c34)"></div>
        <h4>Sed ut perspiciatis unde omnis</h4>
        <p>Ut enim ad minim veniam, quis nostrud exercitation ullamco laboris nisi ut aliquip ex ea commodo consequat.</p>
        <div class="actions"><span>♥ Like</span><span>✎ Comment</span><span>↗ Share</span></div>
        <div class="comment"><div class="avatar"></div>Write a comment...</div>
      </article>
      <article class="box post" style="height:660px">
        <div class="author"><div class="avatar"></div><div><div class="name">Dale Ortiz ▾</div><div class="meta">Shared 4 photos · 5 hours ago</div></div></div>
        <p>Lorem ipsum dolor sit amet, consectetur adipiscing elit, sed do eiusmod tempor incididunt ut labore et dolore magna aliqua.</p>
        <div class="collage">
          <div class="big" role="img" aria-label="Friends toasting at a pizza party" style="background:linear-gradient(160deg,#b88a66,#6e4630)"></div>
          <div role="img" aria-label="Deep dish pizza close-up" style="background:linear-gradient(135deg,#c9613e,#8a3a24)"></div>
          <div role="img" aria-label="Pizza slices on a table" style="background:linear-gradient(135deg,#d08a50,#9a5a30)"></div>
          <div role="img" aria-label="Pizza with basil" style="background:linear-gradient(135deg,#b85a38,#6e3420)"></div>
        </div>
        <h4>Sed ut perspiciatis unde omnis</h4>
        <p>Ut enim ad minim veniam, quis nostrud exercitation ullamco laboris nisi ut aliquip ex ea commodo consequat.</p>
        <div class="actions"><span>♥ Like</span><span>✎ Comment</span><span>↗ Share</span></div>
      </article>
    </div>

    <div class="col-side">
      <section class="box" style="height:450px">
        <h3>Fun stories</h3>
        <div class="list-item story"><div class="thumb" role="img" aria-label="Story photo" style="background:#b06a46"></div><div class="text"><div class="title">Excepteur sint</div><div class="sub">Sunt in culpa qui</div></div><svg viewBox="0 0 14 14"><path d="M1 3h12v7H5l-3 3V10H1z" fill="#999"/></svg></div>
        <div class="list-item story"><div class="thumb" role="img" aria-label="Story photo" style="background:#9e5a3c"></div><div class="text"><div class="title">Excepteur sint</div><div class="sub">Sunt in culpa qui</div></div><svg viewBox="0 0 14 14"><path d="M1 3h12v7H5l-3 3V10H1z" fill="#999"/></svg></div>
        <div class="list-item story"><div class="thumb" role="img" aria-label="Story photo" style="background:#c27850"></div><div class="text"><div class="title">Excepteur sint</div><div class="sub">Sunt in culpa qui</div></div><svg viewBox="0 0 14 14"><path d="M1 3h12v7H5l-3 3V10H1z" fill="#999"/></svg></div>
        <div class="list-item story"><div class="thumb" role="img" aria-label="Story photo" style="background:#a86446"></div><div class="text"><div class="title">Excepteur sint</div><div class="sub">Sunt in culpa qui</div></div><svg viewBox="0 0 14 14"><path d="M1 3h12v7H5l-3 3V10H1z" fill="#999"/></svg></div>
        <div class="list-item story"><div class="thumb" role="img" aria-label="Story photo" style="background:#b4704a"></div><div class="text"><div class="title">Excepteur sint</div><div class="sub">Sunt in culpa qui</div></div><svg viewBox="0 0 14 14"><path d="M1 3h12v7H5l-3 3V10H1z" fill="#999"/></svg></div>
        <div class="list-item story"><div class="thumb" role="img" aria-label="Story photo" style="background:#985638"></div><div class="text"><div class="title">Excepteur sint</div><div class="sub">Sunt in culpa qui</div></div><svg viewBox="0 0 14 14"><path d="M1 3h12v7H5l-3 3V10H1z" fill="#999"/></svg></div>
        <div class="list-item story" style="border:0"><div class="thumb" role="img" aria-label="Story photo" style="background:#bc7248"></div><div class="text"><div class="title">Excepteur sint</div><div class="sub">Sunt in culpa qui</div></div><svg viewBox="0 0 14 14"><path d="M1 3h12v7H5l-3 3V10H1z" fill="#999"/></svg></div>
        <span class="see-all">See all stories ›</span>
      </section>
      <section class="box" style="height:660px">
        <h3>Employee news</h3>
        <div class="list-item story"><div class="thumb" role="img" aria-label="Employee portrait" style="background:#c4a48c"></div><div class="text"><div class="title">Nina Hale</div><div class="stars">★★★<i>★★</i></div></div><svg viewBox="0 0 14 14"><path d="M1 3h12v7H5l-3 3V10H1z" fill="#999"/></svg></div>
        <div class="list-item story"><div class="thumb" role="img" aria-label="Employee portrait" style="background:#b8967c"></div><div class="text"><div class="title">Owen Dale</div><div class="stars">★★★★<i>★</i></div></div><svg viewBox="0 0 14 14"><path d="M1 3h12v7H5l-3 3V10H1z" fill="#999"/></svg></div>
        <div class="list-item story"><div class="thumb" role="img" aria-label="Employee portrait" style="background:#caa88e"></div><div class="text"><div class="title">Nina Hale</div><div class="stars">★★★<i>★★</i></div></div><svg viewBox="0 0 14 14"><path d="M1 3h12v7H5l-3 3V10H1z" fill="#999"/></svg></div>
        <div class="list-item story"><div class="thumb" role="img" aria-label="Employee portrait" style="background:#a88a72"></div><div class="text"><div class="title">Owen Dale</div><div class="stars">★★★★<i>★</i></div></div><svg viewBox="0 0 14 14"><path d="M1 3h12v7H5l-3 3V10H1z" fill="#999"/></svg></div>
        <div class="list-item story"><div class="thumb" role="img" aria-label="Employee portrait" style="background:#c09c82"></div><div class="text"><div class="title">Nina Hale</div><div class="stars">★★★<i>★★</i></div></div><svg viewBox="0 0 14 14"><path d="M1 3h12v7H5l-3 3V10H1z" fill="#999"/></svg></div>
        <div class="list-item story"><div class="thumb" role="img" aria-label="Employee portrait" style="background:#b29278"></div><div class="text"><div class="title">Owen Dale</div><div class="stars">★★★★<i>★</i></div></div><svg viewBox="0 0 14 14"><path d="M1 3h12v7H5l-3 3V10H1z" fill="#999"/></svg></div>
        <div class="list-item story"><div class="thumb" role="img" aria-label="Employee portrait" style="background:#c6a286"></div><div class="text"><div class="title">Nina Hale</div><div class="stars">★★★<i>★★</i></div></div><svg viewBox="0 0 14 14"><path d="M1 3h12v7H5l-3 3V10H1z" fill="#999"/></svg></div>
        <div class="list-item story"><div class="thumb" role="img" aria-label="Employee portrait" style="background:#ac8e76"></div><div class="text"><div class="title">Owen Dale</div><div class="stars">★★★★<i>★</i></div></div><svg viewBox="0 0 14 14"><path d="M1 3h12v7H5l-3 3V10H1z" fill="#999"/></svg></div>
        <div class="list-item story"><div class="thumb" role="img" aria-label="Employee portrait" style="background:#bea088"></div><div class="text"><div class="title">Nina Hale</div><div class="stars">★★★<i>★★</i></div></div><svg viewBox="0 0 14 14"><path d="M1 3h12v7H5l-3 3V10H1z" fill="#999"/></svg></div>
        <div class="list-item story" style="border:0"><div class="thumb" role="img" aria-label="Employee portrait" style="background:#b09078"></div><div class="text"><div class="title">Owen Dale</div><div class="stars">★★★★<i>★</i></div></div><svg viewBox="0 0 14 14"><path d="M1 3h12v7H5l-3 3V10H1z" fill="#999"/></svg></div>
        <span class="see-all">See all employee news ›</span>
      </section>
    </div>
  </div>
</main>

<section class="partners" aria-label="Partner brands">
  <div class="badge" style="width:170px"></div>
  <div class="badge" style="width:120px;border-radius:50%"></div>
  <div class="badge" style="width:70px;border-radius:50%"></div>
</section>

<footer class="site-footer">
  <div class="links"><span>Home</span>|<span>Contact</span>|<span>Topics</span>|<span>Posts and Comments</span>|<span>Discussion</span>|<span>Website Links</span></div>
  <div class="social"><span></span><span></span><span></span><span></span><span></span></div>
  <div class="copy">Copyright © 2017 Bim-Zee. All Rights Reserved</div>
  <span class="to-top">▲</span>
</footer>

</body>
</html>
```